Need CATCHY/VIVID Banner design for my new UTV/ATV/Off Road Vehicle turn signal/lighting company

I need a banner ad designed so I can advertise on several different ATV (all terrain vehicle), UTV (Utility Vehicles), Golf Cart and Off-Road Vehicle forums. Ads need to be very catchy and produce a call to action. Action is getting hits to my website. Our main business is selling turn signal kits to make your side by side or your ATV/UTV street legal, as some states now allow you to drive these on public roads if you have the following items: Turn Signals, Horn, Lighted license plate bracket, headlights and brake lights. We sell all of these items for just about any model vehicle out there. Our call to action for this banner would be to get more website visits.

Target Market(s)

Off-road/outdoor enthusiasts,

Industry/Entity Type

Car Accessorie

Font styles to use
Sans Serif

Requirements
Must have
• Ad size need to be either 728x90 or 300x250. Colorful ad with an off-road vehicle integrated to the design (think UTV, side-by-side, etc.
Nice to have
• Nice to haves would be anything that makes this banner ad stand out on very boring web pages.
Should not have
• anything dull

```html
<!DOCTYPE html>
<html lang="en">
<head>
<meta charset="utf-8">
<title>Ridgeline Signal Co. – ATV & UTV Signal Kits and Lighting</title>
<link rel="stylesheet" href="https://fonts.googleapis.com/css2?family=Oswald:wght@500;600;700&display=swap">
<style>
  :root {
    --ink-dark: #1a0608;
    --red-deep: #7a0a12;
    --red-main: #d3121f;
    --red-bright: #ee2a34;
    --white: #ffffff;
    --yellow: #f7c600;
    --vehicle-grey: #8e9094;
    --vehicle-orange: #e0471c;
  }
  * { margin: 0; padding: 0; box-sizing: border-box; }
  html, body { width: 1200px; height: 1000px; overflow: hidden; }
  body { font-family: "Oswald", "Arial Narrow", sans-serif; background: var(--ink-dark); }

  .banner {
    position: relative;
    width: 1200px;
    height: 1000px;
    overflow: hidden;
    background:
      radial-gradient(ellipse 70% 55% at 78% 60%, rgba(238,42,52,0.55), transparent 70%),
      linear-gradient(160deg, #2a0a0c 0%, var(--red-deep) 32%, var(--red-main) 62%, var(--red-bright) 100%);
  }

  .terrain-backdrop {
    position: absolute;
    inset: 0;
    background:
      linear-gradient(200deg, rgba(255,255,255,0.08) 0%, transparent 35%),
      linear-gradient(175deg, transparent 55%, rgba(120,8,16,0.35) 75%, transparent 100%);
  }

  .brand {
    position: absolute;
    left: 60px;
    top: 52px;
    display: flex;
    align-items: center;
    gap: 22px;
  }
  .brand-mark {
    width: 44px;
    height: 44px;
    border-radius: 50%;
    background: var(--white);
  }
  .brand-name {
    font-weight: 600;
    font-size: 50px;
    letter-spacing: 2px;
    color: var(--white);
    text-transform: uppercase;
    line-height: 1;
  }

  .vehicle-photo {
    position: absolute;
    left: 500px;
    top: 180px;
    width: 700px;
    height: 820px;
    border-radius: 120px 0 0 60px;
    background:
      radial-gradient(ellipse 40% 30% at 55% 30%, rgba(224,71,28,0.85), transparent 70%),
      radial-gradient(ellipse 55% 40% at 55% 55%, rgba(142,144,148,0.8), transparent 75%),
      radial-gradient(ellipse 60% 30% at 50% 88%, rgba(26,26,28,0.9), transparent 75%);
  }

  .headline {
    position: absolute;
    left: 68px;
    top: 322px;
    font-weight: 700;
    font-size: 94px;
    line-height: 1.02;
    color: var(--white);
    text-transform: uppercase;
    letter-spacing: 1px;
  }
  .subhead {
    position: absolute;
    left: 70px;
    top: 552px;
    font-weight: 500;
    font-size: 54px;
    line-height: 1.12;
    color: var(--yellow);
    text-transform: uppercase;
    letter-spacing: 1px;
  }

  .feature-icons {
    position: absolute;
    left: 70px;
    top: 782px;
    display: flex;
    gap: 34px;
    list-style: none;
  }
  .feature-icon {
    width: 96px;
    height: 96px;
    border-radius: 50%;
    background: var(--red-main);
    display: flex;
    align-items: center;
    justify-content: center;
    box-shadow: 0 0 0 2px rgba(255,255,255,0.12);
  }
  .feature-icon svg { width: 62px; height: 62px; }
</style>
</head>
<body>
<main class="banner">
  <div class="terrain-backdrop" role="img" aria-label="Red-tinted mountain landscape backdrop"></div>

  <header class="brand">
    <span class="brand-mark"></span>
    <span class="brand-name">Ridgeline Signal Co.</span>
  </header>

  <div class="vehicle-photo" role="img" aria-label="Grey and orange side-by-side UTV with roll cage, seen from the front"></div>

  <h1 class="headline">ATV&amp; UTV<br>Vechicle</h1>
  <p class="subhead">Signal Kits<br>and Lighting</p>

  <ul class="feature-icons">
    <li class="feature-icon" aria-label="Brake lights">
      <svg viewBox="0 0 60 60" fill="none" stroke="#fff" stroke-width="4" stroke-linecap="round">
        <circle cx="30" cy="30" r="13"/>
        <path d="M14 16 A20 20 0 0 0 14 44"/>
        <path d="M46 16 A20 20 0 0 1 46 44"/>
        <line x1="30" y1="23" x2="30" y2="31"/>
        <circle cx="30" cy="37" r="1.2" fill="#fff"/>
      </svg>
    </li>
    <li class="feature-icon" aria-label="Headlights">
      <svg viewBox="0 0 60 60" fill="none" stroke="#fff" stroke-width="4" stroke-linecap="round">
        <path d="M30 16 C40 16 44 23 44 30 C44 37 40 44 30 44 Z" fill="#fff"/>
        <line x1="10" y1="20" x2="23" y2="20"/>
        <line x1="10" y1="27" x2="23" y2="27"/>
        <line x1="10" y1="34" x2="23" y2="34"/>
        <line x1="10" y1="41" x2="23" y2="41"/>
      </svg>
    </li>
    <li class="feature-icon" aria-label="Horn">
      <svg viewBox="0 0 60 60" fill="#fff">
        <path d="M10 26 L22 26 L46 14 L46 46 L22 34 L10 34 Z"/>
        <rect x="20" y="34" width="6" height="10" rx="2"/>
      </svg>
    </li>
    <li class="feature-icon" aria-label="Turn signals">
      <svg viewBox="0 0 60 60" fill="none" stroke="#fff" stroke-width="3.5" stroke-linejoin="round">
        <path d="M6 30 L18 19 L18 25 L26 25 L26 35 L18 35 L18 41 Z"/>
        <path d="M54 30 L42 19 L42 25 L34 25 L34 35 L42 35 L42 41 Z"/>
      </svg>
    </li>
  </ul>
</main>
</body>
</html>
```